WTF!!! We need a modern professional website for a business litigation law firm.

We need a modern, clean, professional and uncomplicated website for a new business trial and litigation law firm called "Haverlock Trial Firm PLLC". Website must be mobile optimized for iPad and smartphone. The law firm specializes in counseling and representing large corporations, small businesses and entrepreneurs in and out of the courtroom. Lawyers in the firm serve as Florida counsel and trial counsel to organizations facing claims involving product liability, premises liability, professional liability, vehicle and transportation liability, warranty claims, construction defects and delay claims, complex business disputes, commercial litigation and bid disputes in State and Federal Courts. The website is mainly to provide information about the firm, and should include sections describing the firm, identifying the Industries Served and Areas of Practice ," a separate page identifying the "Professionals", a separate page for "Resources & Advisories," and a traveling "Connect With Us" button a site visitor can click on that will launch an email to the Firm's general email account. The website should allow us to easily modify the content on these pages, and let us add/modify links to external information sources. We will not sell anything or take payments through the website. We do need to be able to easily upload and update photographs of attorneys and add new attorneys names/email hyperlinks as the firm grows. We would like to add developments in the law or success stories easily and quickly, such as through a blog page. On the "Connect With Us" page the website should have hyperlinks to email the Firm, and there should be hyperlinks to email each professional on the "Professionals" page. The website should be viewable on mobile devices without distortion. The law firm focuses on trial work and should have some imagery associated with courtrooms, but the overall theme of the site should be modern, clean, and communicate sophistication and strength. The website should be made in Wordpress. We have uploaded logo files for Haverlock Trial Firm.

Target Market(s)

Corporations and companies that are looking for legal representation. Other attorneys/legal industry.

Industry/Entity Type

Legal Industry

Coding

Coded - Design and coding required

Number of Pages Required

1 page

Font styles to use
Sans Serif

Requirements
Must have
• Simple, clean, sophisticated, modern website that includes the logo, watermark of logo, and the elements described above.
Nice to have
• Pictures of city scape, buildings, courtroom, team members.

```html
<!DOCTYPE html>
<html lang="en">
<head>
<meta charset="utf-8">
<title>Haverlock Trial Firm PLLC</title>
<link href="https://fonts.googleapis.com/css2?family=Oswald:wght@500;600;700&family=Lato:wght@400;700;900&display=swap" rel="stylesheet">
<style>
:root{
  --green:#6d8b2b;
  --green-dark:#58731f;
  --green-light:#e6efd2;
  --ink:#1d1d1d;
  --charcoal:#262626;
  --text:#555;
  --white:#fff;
  --star:#e8762b;
}
*{margin:0;padding:0;box-sizing:border-box}
html,body{width:1200px;height:4669px;overflow:hidden}
body{position:relative;font-family:'Lato',sans-serif;color:var(--text);background:var(--white)}
.abs{position:absolute}
.heading{font-family:'Oswald',sans-serif;font-weight:700;text-transform:uppercase;color:var(--ink);letter-spacing:-.5px}
.heading em{font-style:normal;color:var(--green)}
.center{left:0;width:1200px;text-align:center}
.sub{font-size:15px;color:#555}
.btn{position:absolute;display:flex;align-items:center;justify-content:center;font-weight:700;font-size:14px;color:var(--white);background:var(--green);clip-path:polygon(6% 0,100% 0,94% 100%,0 100%);}
.btn::before{content:"";position:absolute;left:10px;top:0;width:9px;height:100%;background:var(--green-light);transform:skewX(-20deg)}
.btn.dark{background:var(--charcoal)}
.btn.dark::before{background:var(--green)}
.mark-bar{position:absolute;left:570px;width:60px;height:6px;background:var(--green);transform:skewX(-25deg)}
.mark-bar.light{background:var(--white)}

/* header */
.topline{left:0;top:0;width:1200px;height:4px;background:var(--green)}
.phone-box{left:112px;top:33px;width:52px;height:44px;background:var(--green);clip-path:polygon(0 0,100% 0,100% 100%,20% 100%);display:flex;align-items:center;justify-content:center}
.call-label{left:180px;top:31px;font-size:11px;font-weight:700;color:var(--ink)}
.call-num{left:180px;top:53px;font-size:17px;font-weight:700;color:var(--ink)}
.brand{left:450px;top:40px;width:300px;text-align:center;font-family:'Lato',sans-serif;font-weight:900;color:var(--ink);font-size:24px;line-height:30px;letter-spacing:1px}
.brand.footer{color:var(--white);font-size:38px;line-height:46px;top:4330px;width:400px;left:400px}
.nav a{position:absolute;top:117px;font-size:13px;font-weight:900;color:var(--ink);text-decoration:none;text-transform:uppercase}
.nav a.active{color:var(--green)}
.nav a.active::after{content:"";position:absolute;left:0;right:0;bottom:-5px;height:2px;background:var(--green)}

/* hero */
.hero{left:0;top:160px;width:1200px;height:583px;background:linear-gradient(90deg,#1c1c1c 0%,#2e2e2e 40%,#6a6a6a 70%,#3b3b3b 100%)}
.hero-eyebrow{left:110px;top:262px;font-family:'Oswald',sans-serif;font-weight:600;font-size:19px;color:var(--green)}
.hero-title{left:110px;top:292px;font-size:50px;line-height:62px;color:var(--white)}
.hero-text{left:111px;top:422px;font-size:14px;line-height:26px;color:#eee}

/* industries */
.card{position:absolute;top:912px;width:250px;height:277px;background:var(--white);box-shadow:0 4px 22px rgba(0,0,0,.09);text-align:center}
.card.on{border-bottom:3px solid var(--green)}
.card .icon{position:absolute;left:92px;top:34px;width:66px;height:64px}
.card h3{position:absolute;left:0;top:115px;width:100%;font-size:17px}
.card p{position:absolute;top:147px;left:18px;width:214px;font-size:13px;line-height:24px;color:#666}
.card .more{position:absolute;left:0;top:224px;width:100%;font-size:12px;font-weight:700;color:var(--green);text-decoration:underline}

/* who */
.green-band{left:0;top:1530px;width:1200px;height:886px;background:var(--green);clip-path:polygon(0 6%,100% 0,100% 100%,0 100%)}
.who-box{left:163px;top:1272px;width:874px;height:403px;background:var(--white);box-shadow:0 6px 26px rgba(0,0,0,.12)}
.who-photo{left:5px;top:4px;width:427px;height:395px;background:linear-gradient(135deg,#3a3027,#8a7b6b 55%,#2b2b2b)}
.who-title{left:484px;top:110px;font-size:36px}
.who-text{left:484px;top:177px;width:350px;font-size:13px;line-height:26px;color:#666}

/* practice */
.pa-title{top:1788px;font-size:38px;color:var(--white)}
.pa-sub{top:1851px;color:#f1f5e6}
.pa-item{position:absolute}
.pa-icon{position:absolute;left:0;top:0;width:108px;height:88px;background:var(--white);clip-path:polygon(0 0,88% 0,100% 100%,12% 100%)}
.pa-icon svg{position:absolute;left:30px;top:18px}
.pa-item h4{position:absolute;left:130px;top:10px;white-space:nowrap;font-family:'Oswald',sans-serif;font-weight:600;font-size:17px;color:var(--white);text-transform:uppercase}
.pa-item p{position:absolute;left:130px;top:41px;width:270px;font-size:13px;line-height:22px;color:#f1f5e6}

/* newsletter */
.newsletter{left:0;top:2416px;width:1200px;height:360px;background:linear-gradient(120deg,#1f1f1f,#2c2c2c 50%,#1a1a1a)}
.input{left:321px;top:2634px;width:360px;height:40px;background:var(--white);clip-path:polygon(0 0,100% 0,97% 100%,0 100%);font-size:12px;color:#777;padding:13px 0 0 30px}

/* news */
.news-card{left:141px;top:3031px;width:921px;height:460px;background:var(--green-light);box-shadow:0 6px 24px rgba(0,0,0,.1)}
.news-photo{left:2px;top:2px;width:513px;height:456px;background:linear-gradient(135deg,#7b6d5c,#c9c2b6 45%,#3c4047)}
.date{left:646px;top:45px;width:143px;height:40px;background:var(--green);color:var(--white);font-size:15px;clip-path:polygon(8% 0,100% 0,100% 100%,0 100%);display:flex;align-items:center;justify-content:center}
.news-title{left:555px;top:104px;width:330px;text-align:center;font-size:18px;line-height:31px}
.news-text{left:555px;top:176px;width:330px;text-align:center;font-size:13px;line-height:26px;color:#666}
.circle{position:absolute;width:40px;height:40px;border-radius:50%;display:flex;align-items:center;justify-content:center}
.circle.grey{background:#c7c9c2}
.circle.black{background:var(--ink)}

/* testimonials */
.testi-bg{left:0;top:3540px;width:1200px;height:660px;background:linear-gradient(180deg,#fff,#f2f2f2 60%,#ebebeb)}
.t-card{position:absolute;top:3692px;width:294px;height:376px;background:var(--white);box-shadow:0 4px 20px rgba(0,0,0,.07)}
.t-card.on{border-bottom:3px solid var(--green)}
.t-quote{position:absolute;left:-26px;top:33px;width:50px;height:50px;border-radius:50%;background:var(--green);color:var(--white);font-family:'Oswald',sans-serif;font-size:34px;text-align:center;line-height:56px}
.stars{position:absolute;left:44px;top:26px;color:var(--star);font-size:13px;letter-spacing:1px}
.t-card p{position:absolute;left:44px;top:58px;width:224px;font-size:13px;line-height:26px;color:#666}
.t-card hr{position:absolute;left:44px;top:279px;width:224px;border:0;border-top:1px solid #e2e2e2}
.avatar{position:absolute;left:42px;top:303px;width:40px;height:40px;border-radius:50%;background:linear-gradient(135deg,#9aa3ad,#3c4450)}
.t-name{position:absolute;left:103px;top:302px;font-family:'Oswald',sans-serif;font-weight:600;font-size:16px;color:var(--green)}
.t-role{position:absolute;left:103px;top:328px;font-size:11px;color:#777}

/* footer */
.footer{left:0;top:4232px;width:1200px;height:437px;background:#111}
.fnav a{position:absolute;top:4487px;font-size:12px;font-weight:700;color:var(--white);text-decoration:none;transform:translateX(-50%);white-space:nowrap}
.ficon{position:absolute;top:4546px;width:52px;height:44px;background:var(--green);clip-path:polygon(0 0,100% 0,100% 100%,18% 100%);display:flex;align-items:center;justify-content:center}
.flabel{position:absolute;top:4542px;font-size:12px;font-weight:700;color:var(--white)}
.fval{position:absolute;top:4562px;font-size:18px;font-weight:700;color:var(--white)}
.social{position:absolute;width:46px;height:40px;background:var(--green);clip-path:polygon(10% 0,100% 0,90% 100%,0 100%)}
.copy{top:4636px;font-size:11px;color:#ddd}
.ico{fill:none;stroke:var(--green);stroke-width:2;stroke-linecap:round;stroke-linejoin:round}
.ico-dark{fill:none;stroke:var(--ink);stroke-width:2;stroke-linecap:round;stroke-linejoin:round}
</style>
</head>
<body>

<!-- Header -->
<div class="abs topline"></div>
<div class="abs phone-box"><svg width="16" height="16" viewBox="0 0 24 24"><path fill="#fff" d="M6.6 10.8a15.5 15.5 0 006.6 6.6l2.2-2.2c.3-.3.7-.4 1-.2 1.1.4 2.3.6 3.6.6.6 0 1 .4 1 1V20c0 .6-.4 1-1 1A17 17 0 013 4c0-.6.4-1 1-1h3.5c.6 0 1 .4 1 1 0 1.3.2 2.5.6 3.6.1.3 0 .7-.2 1z"/></svg></div>
<div class="abs call-label">Call Us:</div>
<div class="abs call-num">+1 555 014 2290</div>
<div class="abs brand">HAVERLOCK<br>TRIAL FIRM</div>
<a class="btn" style="left:892px;top:33px;width:196px;height:44px">Connect With Us</a>
<nav class="nav">
  <a class="active" style="left:109px">Home</a>
  <a style="left:198px">Practice Areas</a>
  <a style="left:363px">Professionals</a>
  <a style="left:721px">Blog</a>
  <a style="left:803px">Resources &amp; Advisories</a>
  <a style="left:1035px">About</a>
</nav>

<!-- Hero -->
<div class="abs hero" role="img" aria-label="Two smiling business professionals reviewing work on a laptop in a modern office"></div>
<div class="abs hero-eyebrow">HAVERLOCK TRIAL FIRM</div>
<h1 class="abs heading hero-title">Driven by excellence,<br>focused on results</h1>
<p class="abs hero-text">Sed ut perspiciatis unde omnis iste natus error sit voluptatem<br>accusantium doloremque laudantium</p>
<a class="btn" style="left:112px;top:493px;width:194px;height:42px">Connect With Us</a>
<svg class="abs" style="left:0;top:600px" width="1200" height="150" viewBox="0 0 1200 150">
  <polygon points="0,30 1200,75 1200,150 0,150" fill="#fff"/>
  <polygon points="0,38 1200,82 1200,92 0,60" fill="#e6efd2"/>
  <polygon points="0,60 1200,92 1200,100 0,146" fill="#6d8b2b"/>
  <polygon points="1160,92 1200,92 1200,150 1140,150" fill="#fff"/>
</svg>

<!-- Industries -->
<div class="mark-bar" style="top:770px"></div>
<h2 class="abs center heading" style="top:800px;font-size:38px">Industries <em>we partner</em> with</h2>
<p class="abs center sub" style="top:860px">Quis autem vel eum iure reprehenderit qui in ea voluptate velit esse quam nihil molestiae consequatur</p>

<div class="card" style="left:196px">
  <svg class="icon" viewBox="0 0 66 64" role="img" aria-label="Office building icon">
    <rect class="ico-dark" x="18" y="4" width="30" height="34"/>
    <path class="ico-dark" d="M24 11h4M32 11h4M40 11h2M24 19h4M32 19h4M40 19h2M24 27h4M32 27h4M40 27h2"/>
    <circle class="ico" cx="14" cy="42" r="5"/><circle class="ico" cx="33" cy="42" r="5"/><circle class="ico" cx="52" cy="42" r="5"/>
    <path class="ico" d="M4 60c0-7 4-10 10-10s10 3 10 10M23 60c0-7 4-10 10-10s10 3 10 10M42 60c0-7 4-10 10-10s10 3 10 10"/>
  </svg>
  <h3 class="heading">Large Corporations</h3><p>Ut enim ad minima veniam, quis no strum exercitationem ullam cor p oris suscipit labori</p><span class="more">Learn More</span></div>
<div class="card on" style="left:475px">
  <svg class="icon" viewBox="0 0 66 64" role="img" aria-label="Invoice and storefront icon">
    <path class="ico-dark" d="M12 4h28l8 8v30M12 4v54h24"/>
    <path class="ico-dark" d="M30 14c-2-2-8-1-7 2s7 2 7 5-6 4-8 2M26 11v15M18 32h22M18 39h14"/>
    <rect class="ico" x="38" y="44" width="22" height="16"/><path class="ico" d="M36 44l4-6h18l4 6M45 60v-8h8v8"/>
  </svg>
  <h3 class="heading">Small Businesses</h3><p>Ut enim ad minima veniam, quis no strum exercitationem ullam cor p oris suscipit labori</p><span class="more">Learn More</span></div>
<div class="card" style="left:756px">
  <svg class="icon" viewBox="0 0 66 64" role="img" aria-label="Entrepreneur network icon">
    <circle class="ico" cx="33" cy="26" r="6"/><path class="ico" d="M22 46c0-8 5-12 11-12s11 4 11 12"/>
    <circle class="ico-dark" cx="33" cy="5" r="3"/><circle class="ico-dark" cx="8" cy="18" r="3"/><circle class="ico-dark" cx="58" cy="18" r="3"/><circle class="ico-dark" cx="8" cy="44" r="3"/><circle class="ico-dark" cx="58" cy="44" r="3"/>
    <path class="ico-dark" d="M33 8v12M11 19l16 5M55 19l-16 5M11 43l11-4M55 43l-11-4M10 60v-8M18 60v-6M48 60v-6M56 60v-8M28 60v-8M38 60v-8"/>
  </svg>
  <h3 class="heading">Entrepreneurs</h3><p>Ut enim ad minima veniam, quis no strum exercitationem ullam cor p oris suscipit labori</p><span class="more">Learn More</span></div>

<!-- Green band + Who we are -->
<div class="abs green-band"></div>
<svg class="abs" style="left:0;top:1490px" width="1200" height="110" viewBox="0 0 1200 110"><polygon points="1200,0 1200,42 700,100 640,100" fill="#262626"/></svg>
<div class="abs who-box">
  <div class="abs who-photo" role="img" aria-label="Attorney and client discussing a document at a desk"></div>
  <div class="mark-bar" style="left:484px;top:72px"></div>
  <h2 class="abs heading who-title">Who <em>we</em> are</h2>
  <p class="abs who-text">Neque porro quisquam est, qui dolorem ipsum quia dolor sit amet, consectetur, adipisci velit, sed quia non numquam eius modi tempora incidunt ut labore et dolore magnam aliquam quaerat voluptatem.</p>
  <a class="btn" style="left:484px;top:298px;width:138px;height:40px">Read More</a>
</div>

<!-- Areas of practice -->
<div class="mark-bar light" style="top:1748px"></div>
<h2 class="abs center heading pa-title">Areas of practice</h2>
<p class="abs center sub pa-sub">Quis autem vel eum iure reprehenderit qui in ea voluptate velit esse quam nihil molestiae consequatur</p>

<div class="pa-item" style="left:130px;top:1905px"><div class="pa-icon">
  <svg width="48" height="52" viewBox="0 0 48 52" role="img" aria-label="Vehicle with umbrella icon">
    <path class="ico" d="M6 18a18 14 0 0136 0zM24 4v-2"/>
    <path class="ico" d="M10 34l4-9h20l4 9M8 34h32v9H8zM12 43v4M36 43v4"/><circle class="ico" cx="14" cy="38.5" r="1.5"/><circle class="ico" cx="34" cy="38.5" r="1.5"/>
  </svg></div><h4>Vehicle and Transportation Liability</h4><p>Quis autem vel eum iure reprehenderit qui in ea voluptate velit esse quam nihil</p></div>
<div class="pa-item" style="left:616px;top:1905px"><div class="pa-icon">
  <svg width="48" height="52" viewBox="0 0 48 52" role="img" aria-label="Professional with badge icon">
    <circle class="ico" cx="22" cy="14" r="9"/><path class="ico" d="M4 50c0-12 8-18 18-18 5 0 9 1 12 4"/>
    <circle class="ico" cx="36" cy="40" r="7"/><path class="ico" d="M33 40l2 2 4-4"/>
  </svg></div><h4>Professional Liability</h4><p>Quis autem vel eum iure reprehenderit qui in ea voluptate velit esse quam nihil</p></div>
<div class="pa-item" style="left:160px;top:2036px"><div class="pa-icon">
  <svg width="48" height="52" viewBox="0 0 48 52" role="img" aria-label="Building with shield icon">
    <path class="ico" d="M6 50V14l18-10 18 10v36z"/><path class="ico" d="M24 22l9 3v8c0 6-4 9-9 11-5-2-9-5-9-11v-8z"/><path class="ico" d="M20 32l3 3 5-5"/>
  </svg></div><h4>Premises Liability</h4><p>Quis autem vel eum iure reprehenderit qui in ea voluptate velit esse quam nihil</p></div>
<div class="pa-item" style="left:647px;top:2036px"><div class="pa-icon">
  <svg width="48" height="52" viewBox="0 0 48 52" role="img" aria-label="Two people in discussion icon">
    <rect class="ico" x="4" y="4" width="16" height="11" rx="2"/><rect class="ico" x="28" y="4" width="16" height="11" rx="2"/>
    <circle class="ico" cx="13" cy="26" r="5"/><circle class="ico" cx="35" cy="26" r="5"/>
    <path class="ico" d="M3 48c0-9 4-14 10-14s10 5 10 14M25 48c0-9 4-14 10-14s10 5 10 14"/>
  </svg></div><h4>Complex Business Disputes</h4><p>Quis autem vel eum iure reprehenderit qui in ea voluptate velit esse quam nihil</p></div>
<div class="pa-item" style="left:190px;top:2166px"><div class="pa-icon">
  <svg width="48" height="52" viewBox="0 0 48 52" role="img" aria-label="Contract document with pen icon">
    <path class="ico" d="M8 4h24l8 8v36H8z"/><path class="ico" d="M14 16h14M14 23h20M14 30h20M14 37h10"/><path class="ico" d="M30 44l12-14 4 3-12 14-5 1z"/>
  </svg></div><h4>Commercial Litigation</h4><p>Quis autem vel eum iure reprehenderit qui in ea voluptate velit esse quam nihil</p></div>
<div class="pa-item" style="left:678px;top:2166px"><div class="pa-icon">
  <svg width="48" height="52" viewBox="0 0 48 52" role="img" aria-label="Warranty shield icon">
    <path class="ico" d="M24 4l17 6v14c0 12-8 20-17 24-9-4-17-12-17-24V10z"/><path class="ico" d="M16 25l6 6 11-11"/>
  </svg></div><h4>Warranty Claims</h4><p>Quis autem vel eum iure reprehenderit qui in ea voluptate velit esse quam nihil</p></div>

<a class="btn dark" style="left:500px;top:2298px;width:194px;height:42px">Connect With Us</a>

<!-- Newsletter -->
<div class="abs newsletter" role="img" aria-label="Dim office background with business people"></div>
<div class="mark-bar light" style="top:2480px"></div>
<h2 class="abs center heading" style="top:2524px;font-size:36px;color:#fff">Join our newsletter</h2>
<p class="abs center sub" style="top:2586px;color:#eee">Quis autem vel eum iure reprehenderit qui in ea voluptate velit esse quam nihil molestiae consequatur</p>
<div class="abs input">Email Address</div>
<a class="btn" style="left:689px;top:2634px;width:190px;height:40px">Subscribe Here</a>
<p class="abs center" style="top:2700px;font-size:10px;font-style:italic;color:#ccc">* Ut enim ad minima veniam, quis nostrum exercitationem ullam</p>
<svg class="abs" style="left:0;top:2762px" width="1200" height="122" viewBox="0 0 1200 122">
  <polygon points="0,0 1200,0 1200,40 0,22" fill="#1f1f1f"/>
  <polygon points="0,22 1200,40 1200,60 0,40" fill="#e6efd2"/>
  <polygon points="0,40 1160,60 0,120" fill="#6d8b2b"/>
</svg>

<!-- News -->
<div class="mark-bar" style="top:2915px"></div>
<h2 class="abs center heading" style="top:2946px;font-size:38px">Latest <em>news and</em> updates</h2>
<div class="abs news-card">
  <div class="abs news-photo" role="img" aria-label="Business team meeting around a table in an office"></div>
  <div class="abs date">01/20/2025</div>
  <h3 class="abs heading news-title">Quis autem vel eum iure reprehenderit qui in ea voluptate velit esse</h3>
  <p class="abs news-text">sed quia non numquam eius modi tempora incidunt ut labore et dolore magnam aliquam quaerat voluptatem.</p>
  <div class="circle grey" style="left:673px;top:375px"><svg width="10" height="10" viewBox="0 0 10 10"><path d="M7 1L3 5l4 4" stroke="#444" stroke-width="1.5" fill="none"/></svg></div>
  <div class="circle black" style="left:725px;top:375px"><svg width="10" height="10" viewBox="0 0 10 10"><path d="M3 1l4 4-4 4" stroke="#fff" stroke-width="1.5" fill="none"/></svg></div>
</div>

<!-- Testimonials -->
<div class="abs testi-bg"></div>
<div class="mark-bar" style="top:3582px"></div>
<h2 class="abs center heading" style="top:3613px;font-size:38px">Our <em>happy</em> customers</h2>

<div class="t-card" style="left:134px"><div class="t-quote">“</div><div class="stars">★★★★☆</div><p>Sed quia non numquam eius modi tempora incidunt ut labore et dolore magnam aliquam quaerat voluptatem. Ut enim ad minima veniam, quis nostrum exercitationem ullam corporis suscipit laboriosam, nisi ut aliquid ex ea commodi</p><hr><div class="avatar" role="img" aria-label="Client portrait"></div><div class="t-name">JANE MERCER</div><div class="t-role">Quis autem vel eum</div></div>
<div class="t-card on" style="left:467px"><div class="t-quote">“</div><div class="stars">★★★★☆</div><p>Sed quia non numquam eius modi tempora incidunt ut labore et dolore magnam aliquam quaerat voluptatem. Ut enim ad minima veniam, quis nostrum exercitationem ullam corporis suscipit laboriosam, nisi ut aliquid ex ea commodi</p><hr><div class="avatar" role="img" aria-label="Client portrait"></div><div class="t-name">JANE MERCER</div><div class="t-role">Quis autem vel eum</div></div>
<div class="t-card" style="left:799px"><div class="t-quote">“</div><div class="stars">★★★★☆</div><p>Sed quia non numquam eius modi tempora incidunt ut labore et dolore magnam aliquam quaerat voluptatem. Ut enim ad minima veniam, quis nostrum exercitationem ullam corporis suscipit laboriosam, nisi ut aliquid ex ea commodi</p><hr><div class="avatar" role="img" aria-label="Client portrait"></div><div class="t-name">JANE MERCER</div><div class="t-role">Quis autem vel eum</div></div>

<div class="circle grey" style="left:553px;top:4104px"><svg width="10" height="10" viewBox="0 0 10 10"><path d="M7 1L3 5l4 4" stroke="#444" stroke-width="1.5" fill="none"/></svg></div>
<div class="circle black" style="left:605px;top:4104px"><svg width="10" height="10" viewBox="0 0 10 10"><path d="M3 1l4 4-4 4" stroke="#fff" stroke-width="1.5" fill="none"/></svg></div>

<!-- Footer -->
<svg class="abs" style="left:0;top:4180px" width="1200" height="60" viewBox="0 0 1200 60">
  <polygon points="0,10 1200,30 1200,40 0,22" fill="#e6efd2"/>
  <polygon points="0,22 1200,40 1200,54 40,54" fill="#6d8b2b"/>
  <polygon points="0,22 40,54 0,54" fill="#111"/>
  <polygon points="0,54 1200,54 1200,60 0,60" fill="#111"/>
</svg>
<div class="abs footer"></div>
<div class="abs brand footer">HAVERLOCK<br>TRIAL FIRM</div>
<nav class="fnav">
  <a style="left:245px">HOME</a>
  <a style="left:371px">PRACTICE AREAS</a>
  <a style="left:527px">PROFESSIONALS</a>
  <a style="left:716px">RESOURCES &amp; ADVISORIES</a>
  <a style="left:913px">CONNECT WITH US</a>
</nav>
<div class="ficon" style="left:189px"><svg width="16" height="16" viewBox="0 0 24 24"><path fill="#fff" d="M6.6 10.8a15.5 15.5 0 006.6 6.6l2.2-2.2c.3-.3.7-.4 1-.2 1.1.4 2.3.6 3.6.6.6 0 1 .4 1 1V20c0 .6-.4 1-1 1A17 17 0 013 4c0-.6.4-1 1-1h3.5c.6 0 1 .4 1 1 0 1.3.2 2.5.6 3.6.1.3 0 .7-.2 1z"/></svg></div>
<div class="flabel" style="left:255px">Call Us:</div>
<div class="fval" style="left:255px">+1 555 014 2290</div>
<div class="ficon" style="left:464px"><svg width="18" height="14" viewBox="0 0 18 14"><rect x="1" y="1" width="16" height="12" fill="#fff"/><path d="M1 1l8 6 8-6" stroke="#6d8b2b" stroke-width="1.5" fill="none"/></svg></div>
<div class="flabel" style="left:531px">Email Us:</div>
<div class="fval" style="left:531px">info@haverlocktrial.com</div>
<div class="ficon" style="left:723px"><svg width="14" height="18" viewBox="0 0 14 18"><path fill="#fff" d="M7 0a7 7 0 00-7 7c0 5 7 11 7 11s7-6 7-11a7 7 0 00-7-7zm0 9.5A2.5 2.5 0 117 4.5a2.5 2.5 0 010 5z"/></svg></div>
<div class="flabel" style="left:792px">Address:</div>
<div class="fval" style="left:792px">Haverlock Trial Firm, USA</div>
<div class="social" style="left:1098px;top:4466px"></div>
<div class="social" style="left:1108px;top:4522px"></div>
<div class="social" style="left:1118px;top:4578px"></div>
<p class="abs center copy">(C) Copyright | All Rights Reserved</p>

</body>
</html>
```